Business Cards Design for the electrical wholesaler: clean bold dynamic :)

We need a business card design that would follow our latest brand guidelines. As an electrical wholesaler we want to bring a fresh look and feel into the industry. The design should be clean bold and dynamic. It should come alive with the renewed energy of our green colour. Our grey colour should keep things balanced and complement the notion of maturity and responsibility. We employ Lato as a corporate font however are not bound by this font and we’re open to interpretation here.

Target Market(s)

Electrical contractors

Industry/Entity Type

Business

Contact Information for Business Card

Logo
Name & Surname: Halyna Dorosh
Job Title: Director of Marketing
Email: halya.dorosh@quillmail.example
Cell phone: XXX.XXX.XXXX
Address: 20517 - 87 Ave. Edmonton, AB, Canada. T6K 4N8
Business Phone: 780.555.0184
Website: www.brovix.example

Font styles to use
Other font styles liked:
• Lato

Requirements
Must have
• Logo & website
Nice to have
• Brand elements - some of them you may find in the attached Brand Guidelines (e.g. three lines on the background signifying "W")

```html
<!DOCTYPE html>
<html lang="en">
<head>
<meta charset="utf-8">
<title>Brovix business card</title>
<link href="https://fonts.googleapis.com/css2?family=Work+Sans:wght@400;500&display=swap" rel="stylesheet">
<style>
  :root {
    --backdrop: #1b1b1b;
    --green: #8cc63f;
    --green-light: #9bcf55;
    --grey: #58595b;
    --grey-card: #5f6062;
    --white: #ffffff;
  }
  * { margin: 0; padding: 0; box-sizing: border-box; }
  html, body { width: 1200px; height: 897px; overflow: hidden; background: var(--backdrop); }
  body { position: relative; font-family: "Work Sans", sans-serif; }

  .card {
    position: absolute;
    left: 303px;
    width: 594px;
    height: 339px;
    border-radius: 22px;
    overflow: hidden;
  }
  .card--front { top: 92px; background: var(--white); }
  .card--back { top: 469px; background: var(--grey-card); }

  .front__divider {
    position: absolute; left: 287px; top: 0; width: 6px; height: 100%;
    background: var(--grey);
  }
  .front__panel {
    position: absolute; left: 297px; top: 0; right: 0; height: 100%;
    background: radial-gradient(circle at 70% 15%, var(--green-light), var(--green) 60%);
    color: var(--white);
  }

  .brand {
    position: absolute; display: flex; align-items: center; gap: 10px;
    font-weight: 500; letter-spacing: -0.5px;
  }
  .brand__mark { width: 16px; height: 16px; background: var(--green); }
  .brand--front { left: 0; width: 287px; top: 140px; justify-content: center; color: var(--grey); font-size: 52px; }
  .brand--back { left: 0; width: 100%; top: 138px; justify-content: center; color: var(--white); font-size: 60px; }

  .contact { position: absolute; left: 38px; top: 0; letter-spacing: 0.3px; }
  .contact__name { position: absolute; top: 82px; font-size: 24px; font-weight: 500; white-space: nowrap; }
  .contact__title { position: absolute; top: 112px; font-size: 15px; white-space: nowrap; }
  .contact__address { position: absolute; top: 140px; font-size: 14px; line-height: 19px; white-space: nowrap; }
  .contact__list { position: absolute; top: 186px; list-style: none; font-size: 14px; line-height: 19.5px; }
  .contact__item { display: flex; align-items: center; gap: 10px; white-space: nowrap; }
  .contact__icon { width: 10px; height: 10px; flex: none; }

  .back__web {
    position: absolute; left: 0; width: 100%; top: 297px; text-align: center;
    font-size: 15px; color: var(--white); letter-spacing: 0.6px;
  }
  .back__web-name { color: var(--green); }
</style>
</head>
<body>

<section class="card card--front">
  <div class="brand brand--front"><span class="brand__mark"></span>brovix</div>
  <div class="front__divider"></div>
  <div class="front__panel">
    <div class="contact">
      <p class="contact__name">Halyna Dorosh</p>
      <p class="contact__title">Director of Marketing</p>
      <p class="contact__address">20517 - 87 Ave.<br>Edmonton, AB, Canada. T6K 4N8</p>
      <ul class="contact__list">
        <li class="contact__item">
          <svg class="contact__icon" viewBox="0 0 10 10"><path d="M2 0.5 L3.6 0.5 L4.2 3 L3 3.8 Q4 6.2 6.2 7 L7 5.8 L9.5 6.4 L9.5 8 Q9.5 9.5 8 9.5 Q1 8.8 0.5 2 Q0.5 0.5 2 0.5Z" fill="#fff"/></svg>
          780.555.0184
        </li>
        <li class="contact__item">
          <svg class="contact__icon" viewBox="0 0 10 10"><rect x="2.3" y="0.5" width="5.4" height="9" rx="1" fill="none" stroke="#fff" stroke-width="1"/><circle cx="5" cy="7.8" r="0.6" fill="#fff"/></svg>
          XXX.XXX.XXXX
        </li>
        <li class="contact__item">
          <svg class="contact__icon" viewBox="0 0 10 10"><rect x="0.7" y="2" width="8.6" height="6.2" fill="none" stroke="#fff" stroke-width="1"/><path d="M0.7 2 L5 5.4 L9.3 2" fill="none" stroke="#fff" stroke-width="1"/></svg>
          halya.dorosh@quillmail.example
        </li>
        <li class="contact__item">
          <svg class="contact__icon" viewBox="0 0 10 10"><g fill="none" stroke="#fff" stroke-width="0.9"><circle cx="5" cy="5" r="4.3"/><ellipse cx="5" cy="5" rx="1.9" ry="4.3"/><path d="M0.7 5 H9.3 M1.3 3 H8.7 M1.3 7 H8.7"/></g></svg>
          www.brovix.example
        </li>
      </ul>
    </div>
  </div>
</section>

<section class="card card--back">
  <div class="brand brand--back"><span class="brand__mark"></span>brovix</div>
  <p class="back__web">www.<span class="back__web-name">brovix</span>.example</p>
</section>

</body>
</html>
```